Harbor Ridge Painting Epoxy Flyer

We need a promotional flyer for a new epoxy floor coatings division of our painting company. We do epoxy garage floor coatings and paver sealing. It needs to be based on and very similar to the attached flyer. The garage floor picture needs to look more realistic, and the before and after pavers pictures should look less shiny but still a good contrast. Include attached logo

```html
<!DOCTYPE html>
<html lang="en">
<head>
<meta charset="utf-8">
<title>Harbor Ridge Painting – Garage &amp; Driveway Flyer</title>
<link href="https://fonts.googleapis.com/css2?family=Anton&family=Bebas+Neue&family=Poppins:ital,wght@0,500;0,600;1,600;1,700&display=swap" rel="stylesheet">
<style>
  :root{
    --stage:#b3b3b3;
    --paper:#ffffff;
    --teal:#114a60;
    --teal-deep:#0d3e51;
    --orange:#d2680e;
    --ink:#1d1d1d;
    --rule:#c9d3d8;
  }
  *{box-sizing:border-box;margin:0;padding:0}
  html,body{width:924px;height:1200px;overflow:hidden;background:var(--stage)}
  .flyer{position:absolute;left:175px;top:158px;width:576px;height:864px;background:var(--paper);overflow:hidden;font-family:"Poppins",sans-serif;color:var(--ink)}
  .abs{position:absolute}

  /* hero */
  .hero-photo{left:229px;top:0;width:347px;height:286px;background:linear-gradient(160deg,#d9cdb9 0%,#efe6d6 35%,#c9b79c 65%,#8a6a4c 100%)}
  .hero-fade{left:150px;top:0;width:120px;height:286px;background:linear-gradient(90deg,rgba(255,255,255,1),rgba(255,255,255,0))}
  .brand{left:0;top:0;width:232px;height:84px;display:flex;align-items:center;justify-content:center;gap:7px}
  .brand-dot{width:16px;height:16px;border-radius:50%;background:var(--teal)}
  .brand-name{font-weight:600;font-size:11.5px;letter-spacing:.4px;color:var(--teal);text-transform:uppercase}
  .headline-panel{left:0;top:84px;width:240px;height:175px;background:linear-gradient(90deg,var(--teal) 70%,rgba(17,74,96,.55) 100%)}
  .headline{left:12px;top:92px;width:220px;font-family:"Anton",sans-serif;color:#fff;line-height:.98;text-transform:uppercase}
  .headline .l1{display:block;font-size:57px;letter-spacing:.5px}
  .headline .l2{display:block;font-size:38px;margin-top:2px}
  .tagline{left:0;top:246px;width:236px;height:36px;background:var(--orange);color:#fff;font-weight:500;font-size:12.5px;display:flex;align-items:center;justify-content:center;clip-path:polygon(0 8%,40% 0,100% 10%,98% 50%,100% 92%,55% 100%,0 94%)}

  /* services */
  .svc-head{top:290px;width:270px;height:36px;background:var(--teal);color:#fff;font-family:"Bebas Neue",sans-serif;font-size:22px;letter-spacing:.3px;display:flex;align-items:center;justify-content:center}
  .svc-head.left{left:13px}.svc-head.right{left:296px}
  .shot{top:332px;width:134px;height:133px}
  .shot.garage-before{left:13px;background:linear-gradient(180deg,#e4e4e2 0%,#e4e4e2 18%,#9b9a94 22%,#8a877f 60%,#a09c93 100%)}
  .shot.garage-after{left:149px;background:linear-gradient(180deg,#eef0f1 0%,#eef0f1 18%,#5f6b7a 21%,#8d96a1 30%,#7e8590 100%)}
  .shot.paver-before{left:296px;background:linear-gradient(180deg,#a9b99a 0%,#c9c6bd 12%,#7b766e 30%,#6b665f 100%)}
  .shot.paver-after{left:432px;background:linear-gradient(180deg,#93aa7d 0%,#b8a89a 12%,#7e4f3a 30%,#6a3f2e 100%)}
  .tag{top:465px;width:134px;height:26px;background:var(--orange);color:#fff;font-style:italic;font-weight:700;font-size:12.5px;display:flex;align-items:center;justify-content:center}
  .tag.a{left:13px}.tag.b{left:149px}.tag.c{left:296px}.tag.d{left:432px}

  .benefits{list-style:none;top:501px;width:250px}
  .benefits.left{left:22px}.benefits.right{left:295px;width:280px}
  .benefits li{height:34px;display:flex;align-items:center;gap:10px;font-family:"Bebas Neue",sans-serif;font-size:17.5px;letter-spacing:.1px;color:var(--ink)}
  .benefits li svg{flex:0 0 26px}
  .divider{left:263px;top:497px;width:1px;height:137px;background:var(--rule)}

  .promise{left:0;top:640px;width:576px;height:60px;background:var(--teal-deep);color:#fff;font-family:"Bebas Neue",sans-serif;font-size:22.5px;display:flex;align-items:center;justify-content:center;clip-path:polygon(0 12%,20% 4%,50% 10%,80% 2%,100% 8%,99% 55%,100% 90%,70% 100%,40% 94%,10% 100%,0 92%)}

  .trust{top:706px;height:56px;display:flex;flex-direction:column;align-items:center;justify-content:flex-end;gap:5px;font-size:10px;font-weight:500}
  .trust.t1{left:0;width:146px}.trust.t2{left:146px;width:208px}.trust.t3{left:354px;width:222px}
  .trust-rule{top:706px;width:1px;height:56px;background:var(--rule)}

  .cta{left:0;top:766px;width:576px;height:68px;background:var(--orange);display:flex;align-items:center;justify-content:center;gap:10px;color:#fff;clip-path:polygon(0 8%,30% 0,60% 6%,100% 2%,100% 100%,0 100%)}
  .cta-lead{font-family:"Bebas Neue",sans-serif;font-size:25px;padding-top:6px}
  .cta-phone{font-family:"Anton",sans-serif;font-size:47px;letter-spacing:.5px}
  .footer{left:0;top:834px;width:576px;height:30px;background:var(--teal);color:#fff;font-style:italic;font-weight:700;font-size:14px;display:flex;align-items:center;justify-content:center}
</style>
</head>
<body>
<main class="flyer">
  <div class="abs hero-photo" role="img" aria-label="Photo of a bright home entry with stone tile floor, wood beams and patterned armchairs"></div>
  <div class="abs hero-fade"></div>
  <div class="abs brand"><span class="brand-dot"></span><span class="brand-name">Harbor Ridge Painting</span></div>
  <div class="abs headline-panel"></div>
  <h1 class="abs headline"><span class="l1">Upgrade</span><span class="l2">Your Garage</span><span class="l2">&amp; Driveway</span></h1>
  <p class="abs tagline">From Worn-Out To Like New</p>

  <h2 class="abs svc-head left">Epoxy Garage Floor Coatings</h2>
  <h2 class="abs svc-head right">Paver Sealing</h2>

  <div class="abs shot garage-before" role="img" aria-label="Worn, stained bare concrete garage floor before coating"></div>
  <div class="abs shot garage-after" role="img" aria-label="Garage floor after grey flake epoxy coating"></div>
  <div class="abs shot paver-before" role="img" aria-label="Faded grey paver walkway before sealing"></div>
  <div class="abs shot paver-after" role="img" aria-label="Paver walkway after sealing with rich reddish-brown tones"></div>

  <span class="abs tag a">BEFOR</span><span class="abs tag b">AFTER</span>
  <span class="abs tag c">BEFOR</span><span class="abs tag d">AFTER</span>

  <ul class="abs benefits left">
    <li><svg width="26" height="26" viewBox="0 0 26 26"><circle cx="13" cy="13" r="13" fill="var(--orange)"/><path d="M13 6l6 2v5c0 4-3 6-6 7-3-1-6-3-6-7V8z" fill="none" stroke="#fff" stroke-width="1.4"/><path d="M10 13l2 2 4-4" fill="none" stroke="#fff" stroke-width="1.4"/></svg>Durable, Long-Lasting Finish</li>
    <li><svg width="26" height="26" viewBox="0 0 26 26"><circle cx="13" cy="13" r="13" fill="var(--orange)"/><rect x="8" y="8" width="10" height="10" fill="none" stroke="#fff" stroke-width="1.3"/><path d="M11 8v10M15 8v10M8 11h10M8 15h10" stroke="#fff" stroke-width=".8"/></svg>Slip-Resistant Texture</li>
    <li><svg width="26" height="26" viewBox="0 0 26 26"><circle cx="13" cy="13" r="13" fill="var(--orange)"/><path d="M6 13h14M10 13l-2-4M10 13l-2 4M16 13l2-4M16 13l2 4" fill="none" stroke="#fff" stroke-width="1.4"/></svg>Covers Cracks &amp; Imperfections</li>
    <li><svg width="26" height="26" viewBox="0 0 26 26"><circle cx="13" cy="13" r="13" fill="var(--orange)"/><path d="M8 17l5-7 4 3-4 6zM16 7l1 2M19 9l-2 1" fill="none" stroke="#fff" stroke-width="1.4"/></svg>Easy To Clean &amp; Maintain</li>
  </ul>
  <div class="abs divider"></div>
  <ul class="abs benefits right">
    <li><svg width="26" height="26" viewBox="0 0 26 26"><circle cx="13" cy="13" r="13" fill="var(--orange)"/><path d="M8 14a5 5 0 0 1 9-4M18 12a5 5 0 0 1-9 4" fill="none" stroke="#fff" stroke-width="1.4"/><path d="M17 7v3h-3M9 19v-3h3" fill="none" stroke="#fff" stroke-width="1.3"/></svg>Restores Color &amp; Enhances Appearance</li>
    <li><svg width="26" height="26" viewBox="0 0 26 26"><circle cx="13" cy="13" r="13" fill="var(--orange)"/><circle cx="11" cy="10" r="3" fill="none" stroke="#fff" stroke-width="1.3"/><path d="M15 12l4 1.3v3c0 2.5-2 3.7-4 4.3-2-.6-4-1.8-4-4.3v-3z" fill="#fff"/></svg>Protects From Sun Fading</li>
    <li><svg width="26" height="26" viewBox="0 0 26 26"><circle cx="13" cy="13" r="13" fill="var(--orange)"/><path d="M7 19h12M13 19v-6M13 14l-3-3M13 13l3-4" fill="none" stroke="#fff" stroke-width="1.4"/></svg>Helps Prevent Weeds &amp; Sand Loss</li>
    <li><svg width="26" height="26" viewBox="0 0 26 26"><circle cx="13" cy="13" r="13" fill="var(--orange)"/><path d="M8 17l5-7 4 3-4 6zM16 7l1 2M19 9l-2 1" fill="none" stroke="#fff" stroke-width="1.4"/></svg>Easier To Clean &amp; Maintain</li>
  </ul>

  <p class="abs promise">Practical Upgrades That Protect And Improve Your Home</p>

  <div class="abs trust t1"><svg width="28" height="30" viewBox="0 0 28 30"><rect x="2" y="2" width="18" height="24" rx="1" fill="none" stroke="var(--orange)" stroke-width="2.2"/><path d="M6 8h10M6 12h10M6 16h7" stroke="var(--orange)" stroke-width="2"/><circle cx="21" cy="20" r="6" fill="var(--orange)"/><path d="M18.5 20l2 2 3-3.5" fill="none" stroke="#fff" stroke-width="1.6"/></svg><span>Licensed &amp; Insured</span></div>
  <div class="abs trust-rule" style="left:146px"></div>
  <div class="abs trust t2"><svg width="42" height="28" viewBox="0 0 42 28"><circle cx="12" cy="6" r="5" fill="var(--orange)"/><circle cx="30" cy="6" r="5" fill="var(--orange)"/><circle cx="21" cy="13" r="4" fill="var(--orange)"/><path d="M2 24a10 9 0 0 1 16-7M24 17a10 9 0 0 1 16 7M13 28a8 8 0 0 1 16 0z" fill="var(--orange)"/></svg><span>Family-Owned Local Business</span></div>
  <div class="abs trust-rule" style="left:354px"></div>
  <div class="abs trust t3"><svg width="22" height="28" viewBox="0 0 22 28"><path d="M11 2a8 8 0 0 1 8 8c0 6-8 13-8 13S3 16 3 10a8 8 0 0 1 8-8z" fill="none" stroke="var(--orange)" stroke-width="2.4"/><circle cx="11" cy="10" r="3" fill="var(--orange)"/><path d="M4 26h14" stroke="var(--orange)" stroke-width="2.4"/></svg><span>Serving Prescott &amp; Surrounding Areas</span></div>

  <div class="abs cta"><span class="cta-lead">Call For A Free Estimate</span><span class="cta-phone">928-555-0147</span></div>
  <p class="abs footer">FAST, PROFESSIONAL SERVICE YOU CAN TRUST</p>
</main>
</body>
</html>
```